Business Card for a Jewellery Brand

Business card for an upscale jewellery brand. Attached is the brand logo and icon and color board. I am looking for two card versions: one for the founder and one is generic. The card should be elegant and convey upscale and premium feel. I am open to both square and rectangle card shapes.

Industry/Entity Type

Jewelry

Contact Information for Business Card

Two cards: (1) Sunela Parvaniya (Founder) (2) General
(1) Sunela Parvaniya card should have Name: Sunela Parvaniya, Title: Founder Email id: sunela@quiremo.com.au. Phone no: +61452913307
(2) Generic card should have Email id: info@quiremo.com.au. Phone no: +61436207518

Requirements
Must have
• Workmark
• ICON
• Phone no
• Email ID
• ABN: 58219740312 (Note: ABN is Business number in Australia)
• Website: www.quiremo.com.au
• Instagram: quiremo_jewellery
• Facebook: @quiremojewellery
Nice to have
• Tagline

```html
<!DOCTYPE html>
<html lang="en">
<head>
<meta charset="utf-8">
<title>Quiremo Business Cards</title>
<link href="https://fonts.googleapis.com/css2?family=Montserrat:wght@400;600&family=Open+Sans:wght@400;600&display=swap" rel="stylesheet">
<style>
  :root {
    --stage: #262626;
    --card: #ffffff;
    --blush: #e59a96;
    --ink: #1f1f1f;
    --white: #ffffff;
  }
  * { margin: 0; padding: 0; box-sizing: border-box; }
  html, body {
    width: 1200px; height: 900px; overflow: hidden;
    background: var(--stage);
  }
  .stage { position: relative; width: 1200px; height: 900px; }

  .card {
    position: absolute;
    background: var(--card);
    overflow: hidden;
  }
  .card--front { left: 149px; top: 306px; width: 439px; height: 271px; }
  .card--back  { left: 608px; top: 306px; width: 441px; height: 272px; }

  .front-band { position: absolute; left: 0; top: 0; }

  .wordmark {
    position: absolute;
    font-family: "Montserrat", sans-serif;
    font-weight: 400;
    letter-spacing: 0.14em;
    line-height: 1;
    white-space: nowrap;
  }
  .card--front .wordmark {
    left: 24px; top: 31px;
    font-size: 33px;
    color: var(--white);
  }
  .brand-seal {
    position: absolute;
    left: 309px; top: 36px;
    width: 48px; height: 48px;
    border-radius: 50%;
    border: 3px solid var(--blush);
    background: var(--white);
  }

  .holder { position: absolute; left: 24px; top: 147px; }
  .holder-name {
    font-family: "Montserrat", sans-serif;
    font-weight: 600;
    font-size: 15px;
    color: var(--blush);
    text-transform: uppercase;
    letter-spacing: 0.01em;
  }
  .holder-title {
    font-family: "Open Sans", sans-serif;
    font-size: 12px;
    color: var(--ink);
    margin-top: 0;
  }

  .contact-list {
    position: absolute; left: 24px; top: 203px;
    list-style: none;
    font-family: "Open Sans", sans-serif;
    font-size: 12px;
    color: var(--ink);
  }
  .contact-list li { display: flex; align-items: center; height: 16px; }
  .contact-list svg { width: 9px; height: 9px; margin-right: 5px; fill: var(--blush); }

  .abn {
    position: absolute; right: 27px; top: 187px;
    font-family: "Open Sans", sans-serif;
    font-size: 12px;
    color: var(--ink);
  }
  .abn-label { color: var(--blush); font-weight: 600; }

  .social-list {
    position: absolute; right: 28px; top: 215px;
    list-style: none;
    font-family: "Open Sans", sans-serif;
    font-size: 12px;
    color: var(--ink);
    text-align: right;
  }
  .social-list li { display: flex; justify-content: flex-end; align-items: center; height: 17px; }
  .social-dot {
    display: inline-block; width: 12px; height: 12px;
    border-radius: 50%; background: var(--blush);
    margin-left: 7px;
  }

  .back-lockup {
    position: absolute; left: 0; top: 0; width: 100%; height: 100%;
  }
  .back-seal {
    position: absolute; left: 190px; top: 62px;
    width: 60px; height: 60px;
    border-radius: 50%;
    border: 3px solid var(--blush);
  }
  .card--back .wordmark {
    left: 0; width: 100%; top: 173px;
    text-align: center;
    font-size: 42px;
    color: var(--blush);
    letter-spacing: 0.1em;
    padding-left: 0.1em;
  }
</style>
</head>
<body>
<main class="stage">

  <section class="card card--front" aria-label="Founder card, front">
    <svg class="front-band" width="439" height="271" viewBox="0 0 439 271" aria-hidden="true">
      <polygon points="0,0 439,0 439,86 391,86 333,10 275,86 0,86" fill="var(--blush)"/>
    </svg>
    <div class="wordmark">QUIREMO</div>
    <span class="brand-seal" aria-hidden="true"></span>

    <div class="holder">
      <p class="holder-name">Sunela Parvaniya</p>
      <p class="holder-title">Founder</p>
    </div>

    <p class="abn"><span class="abn-label">ABN:</span> 58219740312</p>

    <ul class="contact-list">
      <li>
        <svg viewBox="0 0 10 10" aria-hidden="true"><path d="M2 0.5 L3.6 2.6 L2.8 3.6 C3.4 5 5 6.6 6.4 7.2 L7.4 6.4 L9.5 8 L8.4 9.5 C4.5 9.3 0.7 5.5 0.5 1.6 Z"/></svg>
        +61452913307
      </li>
      <li>
        <svg viewBox="0 0 10 10" aria-hidden="true"><path d="M0.5 2 H9.5 V8.5 H0.5 Z M1.2 2.6 L5 5.6 L8.8 2.6" stroke="#fff" stroke-width="0.8"/></svg>
        sunela@quiremo.com.au.
      </li>
      <li>
        <svg viewBox="0 0 10 10" aria-hidden="true"><circle cx="5" cy="5" r="4.5"/><path d="M0.5 5 H9.5 M5 0.5 C3 3 3 7 5 9.5 M5 0.5 C7 3 7 7 5 9.5" stroke="#fff" stroke-width="0.7" fill="none"/></svg>
        www.quiremo.com.au
      </li>
    </ul>

    <ul class="social-list">
      <li>@quiremojewellery <span class="social-dot" aria-hidden="true"></span></li>
      <li>quiremo_jewellery <span class="social-dot" aria-hidden="true"></span></li>
    </ul>
  </section>

  <section class="card card--back" aria-label="Card back">
    <div class="back-lockup">
      <span class="back-seal" aria-hidden="true"></span>
      <div class="wordmark">QUIREMO</div>
    </div>
  </section>

</main>
</body>
</html>
```